Tide & Thistle Website Creation For Online Spirits Sales via MerrowVats.com

Want a Website developed that I will use to partner with Merrow Vats to sell my signature rum online. Merrow Vats will add the final code to make the website an e-commerce site. Website should have links to Social media pages, recipies, About, news and events, products. I have he domain name already just need a designer to make the website look professional. Need website capable of being viewed on iPhone and Android devices. Please use the color scheme that is on the label. The brand motto is: Celebrate Life With Family old and new friends. The bottle sent in the images will be replaced with and actual high resolution image of the bottle when it is produce on 27 DEC 21. Can give the selected designer access to develop the website. I have the hostbramble.com domain name. Final code will be added by a designer from MerrowVats.com to make it a e-commerce store.
Updates

I added more information to refine the design I wanted. I should have had this information available to the designers when I started the project.

Target Market(s)

Target Market is 25-50 year old who drink rum

Industry/Entity Type

Spirits. Using Website to sell Rum online

Number of Pages Required

1 page

Font styles to use
Sans Serif

Colors
00AB8E
00BBA5
67D7C9
C6EFE9
E9F9F6

Requirements
Must have
• Must look elegant and of high class. Rum is being market as a premium unnamed rum.
Nice to have
• Video of people drinking, smiling and celebrating

```html
<!DOCTYPE html>
<html lang="en">
<head>
<meta charset="utf-8">
<title>Tide &amp; Thistle — Small Batch Crafted Rum</title>
<link rel="stylesheet" href="https://fonts.googleapis.com/css2?family=Montserrat:wght@400;500;600;700;800&family=Great+Vibes&family=Cinzel:wght@500;600&display=swap">
<style>
:root{
  --teal:#00AB8E;
  --teal-2:#00BBA5;
  --teal-3:#67D7C9;
  --mint:#C6EFE9;
  --mint-2:#E9F9F6;
  --orange:#F7A33A;
  --dark:#1c1f21;
  --ink:#222;
  --grey:#555;
  --white:#fff;
}
*{margin:0;padding:0;box-sizing:border-box}
html,body{width:1200px;height:3831px;overflow:hidden}
body{position:relative;font-family:'Montserrat',sans-serif;color:var(--ink);background:var(--white)}
.abs{position:absolute}
a{text-decoration:none;color:inherit}

/* header */
.site-header{position:absolute;left:0;top:0;width:1200px;height:75px;background:#1a1a1a;z-index:5}
.brand{position:absolute;left:115px;top:10px;display:flex;align-items:center;gap:12px;color:var(--white)}
.brand-mark{width:56px;height:56px;border-radius:50%;border:3px solid var(--white)}
.brand-name{font-size:29px;font-weight:500;letter-spacing:.5px}
.main-nav{position:absolute;top:32px;left:0;width:100%;font-size:12px;font-weight:500;color:var(--white)}
.main-nav a{position:absolute}
.main-nav .active{font-weight:700}
.nav-underline{position:absolute;left:502px;top:74px;width:88px;height:3px;background:var(--teal)}
.nav-icon{position:absolute;top:28px}

/* hero */
.hero{position:absolute;left:0;top:0;width:1200px;height:743px}
.hero-photo{position:absolute;left:12px;top:75px;width:1188px;height:660px;background:linear-gradient(100deg,#14191b 0%,#263036 45%,#3a4247 70%,#20282c 100%)}
.hero-edge{position:absolute;left:0;top:75px;width:12px;height:640px;background:#5b5e60}
.hero-script{position:absolute;left:116px;top:240px;font-family:'Great Vibes',cursive;font-size:66px;color:var(--white);line-height:1}
.hero-title{position:absolute;left:125px;top:312px;font-size:53px;font-weight:800;color:var(--white);line-height:58px;letter-spacing:.5px}
.btn{display:flex;align-items:center;justify-content:center;border-radius:30px;font-weight:700;color:var(--white);text-transform:uppercase}
.hero-btn{position:absolute;left:125px;top:443px;width:180px;height:47px;background:var(--teal);font-size:14px}
.dots{position:absolute;left:560px;top:624px;display:flex;gap:10px}
.dots span{width:15px;height:15px;border-radius:50%;border:2px solid var(--white)}
.dots span.on{background:var(--white)}
.hero-wave{position:absolute;left:0;top:640px}

/* about */
.about-photo-wrap{position:absolute;left:96px;top:812px;width:490px;height:490px}
.about-photo{position:absolute;left:22px;top:22px;width:446px;height:446px;border-radius:50%;background:radial-gradient(circle at 40% 40%,#d84a6a 0%,#6b2b8f 45%,#1d2b77 100%)}
.about-title{position:absolute;left:622px;top:874px;font-size:35px;color:var(--teal);font-weight:400}
.about-title b{color:var(--ink);font-weight:800}
.about-text{position:absolute;left:625px;top:950px;width:520px;font-size:16px;line-height:27.5px;color:var(--grey)}
.about-text p+p{margin-top:26px}
.about-btn{position:absolute;left:614px;top:1178px;width:202px;height:53px;background:var(--teal);font-size:16px}

/* products */
.products{position:absolute;left:0;top:1383px;width:1200px;height:730px;background:linear-gradient(180deg,#35b394 0%,#6cd3c0 70%,#7edbca 100%)}
.section-script{position:absolute;width:100%;text-align:center;font-family:'Great Vibes',cursive;font-size:34px;color:var(--white)}
.section-title{position:absolute;width:100%;text-align:center;font-size:33px;font-weight:400}
.section-title b{font-weight:800}
.title-bar{position:absolute;left:564px;width:72px;height:3px;background:var(--white)}
.product{position:absolute;width:300px;text-align:center;color:var(--white)}
.bottle{margin:0 auto;width:90px;height:268px;border-radius:22px 22px 14px 14px;background:linear-gradient(180deg,#e9e2d4 0%,#d98c2a 35%,#b75c1a 100%)}
.bottle.red{background:linear-gradient(180deg,#e9e2d4 0%,#e05a2a 35%,#b52a1e 100%)}
.product-name{margin-top:30px;font-size:17px;font-weight:700}
.product-desc{margin-top:8px;font-size:12px}
.product-btn{margin:22px auto 0;width:140px;height:38px;border:2px solid var(--white);border-radius:20px;font-size:12px;display:flex;align-items:center;justify-content:center;font-weight:700}
.product-card{position:absolute;left:448px;top:161px;width:307px;height:443px;background:linear-gradient(160deg,#333 0%,#1a1a1a 100%);border:3px solid #1d1d1d}
.product-card::after{content:"";position:absolute;inset:6px;border:1px solid rgba(255,255,255,.5)}
.arrow{position:absolute}

/* recipes */
.recipes-title{position:absolute;left:0;top:2180px;width:100%;text-align:center;font-size:33px;color:var(--teal)}
.recipes-title b{color:var(--ink);font-weight:800}
.recipes-bar{position:absolute;left:564px;top:2230px;width:72px;height:3px;background:var(--teal)}
.recipe{position:absolute;overflow:hidden;border-radius:4px}
.recipe-caption{position:absolute;font-size:12px;font-weight:700;color:var(--white);line-height:18px}
.recipe-main{left:393px;top:2275px;width:443px;height:330px;background:linear-gradient(180deg,#3b3a30 0%,#6b5a34 55%,#2c2a24 100%);box-shadow:0 10px 30px rgba(0,0,0,.35);z-index:2}
.recipe-time{position:absolute;left:575px;top:2508px;width:82px;height:22px;border-radius:12px;background:var(--teal);color:var(--white);font-size:11px;font-weight:700;display:flex;align-items:center;justify-content:center;z-index:3}
.recipe-btn{position:absolute;left:552px;top:2590px;width:129px;height:35px;background:var(--orange);font-size:11px;z-index:3}

/* news */
.news{position:absolute;left:0;top:2736px;width:1200px;height:640px;background:linear-gradient(180deg,#2fb091 0%,#5ccab5 60%,#7cd9c8 100%)}
.news-title{position:absolute;left:143px;top:75px;font-size:33px;color:var(--white)}
.news-title b{font-weight:800}
.news-title-bar{position:absolute;left:143px;top:122px;width:72px;height:3px;background:var(--white)}
.news-card{position:absolute;top:158px;width:308px}
.news-photo{height:206px}
.news-body{position:absolute;left:15px;top:178px;width:278px;height:162px;background:var(--white);text-align:center;box-shadow:0 4px 14px rgba(0,0,0,.12)}
.news-date{position:absolute;left:97px;top:162px;width:114px;height:24px;border-radius:12px;background:var(--mint);color:var(--teal);font-size:11px;font-weight:700;display:flex;align-items:center;justify-content:center;z-index:2}
.news-head{margin-top:38px;font-size:14px;font-weight:500;line-height:19px;color:var(--ink)}
.news-text{margin-top:7px;font-size:10px;line-height:15px;color:#777}
.news-more{margin-top:9px;font-size:11px;font-weight:700;color:var(--teal)}

/* footer */
.footer-brand{position:absolute;left:126px;top:3430px;width:254px;text-align:center}
.footer-mark{width:72px;height:72px;border-radius:50%;border:4px solid var(--ink);margin:0 auto}
.footer-name{margin-top:8px;font-size:32px;font-weight:500;letter-spacing:.5px}
.social{margin-top:16px;display:flex;justify-content:center;gap:7px}
.social span{width:38px;height:38px;border-radius:50%;border:2px solid var(--teal)}
.footer-col{position:absolute;top:3450px}
.footer-col h4{font-family:'Cinzel',serif;font-weight:600;font-size:17px;letter-spacing:.5px;color:var(--ink)}
.footer-col ul{list-style:none;margin-top:22px;font-size:12.5px;color:#444}
.footer-col li{height:29.5px}
.col-rule{position:absolute;width:1px;background:#ddd}
.col-mark{position:absolute;width:3px;height:33px;background:var(--ink)}
.contact li{display:flex;gap:14px;align-items:flex-start;height:auto;margin-bottom:14px;line-height:18px}
.contact svg{flex:none}
.footer-line{position:absolute;left:0;top:3713px;width:1200px;height:1px;background:#e3e3e3}
.copyright{position:absolute;left:0;top:3756px;width:100%;text-align:center;font-size:11px;color:#666}
</style>
</head>
<body>

<!-- hero -->
<section class="hero">
  <div class="hero-photo" role="img" aria-label="Bottle of Tide &amp; Thistle rum beside a gin glass with lime, blueberries and mint, and a cocktail shaker on a dark wet bar"></div>
  <div class="hero-edge"></div>
  <div class="hero-script">Caribbean Rum</div>
  <h1 class="hero-title">SMALL BATCH<br>CRAFTED RUM</h1>
  <a class="btn hero-btn" href="#products">Shop Now</a>
  <div class="dots"><span></span><span class="on"></span><span></span><span></span></div>
  <svg class="hero-wave" width="1200" height="110" viewBox="0 0 1200 110">
    <path d="M0 103 C240 40 520 30 760 55 C950 75 1080 40 1200 20 L1200 110 L0 110 Z" fill="#fff"/>
    <path d="M100 75 C330 40 560 38 760 58 C950 78 1080 45 1200 34" fill="none" stroke="#00AB8E" stroke-width="5"/>
    <line x1="609" y1="18" x2="609" y2="98" stroke="#00AB8E" stroke-width="2"/>
  </svg>
</section>

<header class="site-header">
  <a class="brand" href="#"><span class="brand-mark"></span><span class="brand-name">TIDE &amp; THISTLE</span></a>
  <nav class="main-nav">
    <a class="active" style="left:505px" href="#about">ABOUT US</a>
    <a style="left:627px" href="#products">PRODUCTS</a>
    <a style="left:751px" href="#recipes">RECIPIES</a>
    <a style="left:859px" href="#news">NEWS &amp; EVENT</a>
  </nav>
  <svg class="nav-icon" style="left:1005px" width="20" height="20" viewBox="0 0 20 20"><circle cx="8" cy="8" r="6" fill="none" stroke="#fff" stroke-width="1.6"/><line x1="12.5" y1="12.5" x2="18" y2="18" stroke="#fff" stroke-width="1.6"/></svg>
  <svg class="nav-icon" style="left:1051px" width="20" height="20" viewBox="0 0 20 20"><rect x="3" y="5" width="14" height="13" rx="1.5" fill="none" stroke="#fff" stroke-width="1.6"/><path d="M7 5 V3.5 a3 3 0 0 1 6 0 V5" fill="none" stroke="#fff" stroke-width="1.6"/></svg>
</header>
<div class="nav-underline"></div>

<!-- about -->
<section id="about">
  <div class="about-photo-wrap">
    <svg class="abs" style="left:0;top:0" width="490" height="490" viewBox="0 0 490 490">
      <path d="M245 6 A239 239 0 0 1 380 444" fill="none" stroke="#F7A33A" stroke-width="8"/>
      <path d="M380 444 A239 239 0 0 1 6 245" fill="none" stroke="#F7A33A" stroke-width="8"/>
      <path d="M6 245 A239 239 0 0 1 245 6" fill="none" stroke="#00AB8E" stroke-width="8"/>
      <path d="M30 300 A225 225 0 0 1 245 20" fill="none" stroke="#00AB8E" stroke-width="6"/>
    </svg>
    <div class="about-photo" role="img" aria-label="Friends raising colourful cocktails together at a party"></div>
  </div>
  <h2 class="about-title">ABOUT <b>TIDE &amp; THISTLE</b></h2>
  <div class="about-text">
    <p>Lorem ipsum dolor sit amet, consectetur adipiscing elit, sed do eiusmod tempor incididunt ut labore et dolore magna aliqua. Ut enim ad minim veniam, quis nostrud exercitation ullamco laboris nisi ut aliquip x ea commodo consequat.</p>
    <p>Duis aute irure dolor in reprehenderit in voluptate velit esse cillumectetur adipiscing elit, sed do eiusmod tempor</p>
  </div>
  <a class="btn about-btn" href="#">Learn More</a>
</section>

<!-- products -->
<section class="products" id="products">
  <div class="section-script" style="top:40px">Shop now</div>
  <h2 class="section-title" style="top:75px;color:#fff">OUR <b>PRODUCTS</b></h2>
  <div class="title-bar" style="top:124px"></div>

  <div class="product-card" role="img" aria-label="Bar tools and shaker in black and white behind the bottle"></div>

  <div class="product" style="left:138px;top:183px">
    <div class="bottle red" role="img" aria-label="Tide &amp; Thistle rum bottle, red blend"></div>
    <div class="product-name">TIDE &amp; THISTLE RUM</div>
    <div class="product-desc">Lorem ipsum dolor sit amet conse</div>
    <a class="product-btn" href="#">SHOP NOW</a>
  </div>
  <div class="product" style="left:452px;top:183px">
    <div class="bottle" role="img" aria-label="Tide &amp; Thistle rum bottle, gold blend"></div>
    <div class="product-name">TIDE &amp; THISTLE RUM</div>
    <div class="product-desc">Lorem ipsum dolor sit amet conse</div>
    <a class="product-btn" href="#">SHOP NOW</a>
  </div>
  <div class="product" style="left:770px;top:183px">
    <div class="bottle" role="img" aria-label="Tide &amp; Thistle rum bottle, aged blend"></div>
    <div class="product-name">TIDE &amp; THISTLE RUM</div>
    <div class="product-desc">Lorem ipsum dolor sit amet conse</div>
    <a class="product-btn" href="#" style="margin-top:34px">SHOP NOW</a>
  </div>

  <svg class="arrow" style="left:118px;top:342px" width="26" height="42" viewBox="0 0 26 42"><path d="M22 3 L5 21 L22 39" fill="none" stroke="#fff" stroke-width="5" stroke-linecap="round" stroke-linejoin="round"/></svg>
  <svg class="arrow" style="left:1081px;top:342px" width="26" height="42" viewBox="0 0 26 42"><path d="M4 3 L21 21 L4 39" fill="none" stroke="#fff" stroke-width="5" stroke-linecap="round" stroke-linejoin="round"/></svg>

  <svg class="abs" style="left:0;top:620px" width="1200" height="112" viewBox="0 0 1200 112">
    <path d="M0 92 C300 30 560 80 780 80 C960 80 1100 40 1200 0 L1200 112 L0 112 Z" fill="#fff"/>
    <path d="M80 78 C320 40 560 98 780 96 C960 94 1080 60 1150 36" fill="none" stroke="#F7A33A" stroke-width="7" stroke-linecap="round"/>
  </svg>
</section>

<!-- recipes -->
<section id="recipes">
  <h2 class="recipes-title">OUR <b>RECIEPES</b></h2>
  <div class="recipes-bar"></div>

  <div class="recipe" style="left:180px;top:2314px;width:230px;height:276px;background:linear-gradient(160deg,#5c6a4e 0%,#2f3a2a 60%,#1e241c 100%)" role="img" aria-label="Mojito with mint and crushed ice">
    <div class="recipe-caption" style="left:60px;top:204px;width:200px">LOREM IPSUM DOLOR SIT A<br>&nbsp;&nbsp;&nbsp;&nbsp;&nbsp;&nbsp;&nbsp;ADIPISCING ELIT SED</div>
  </div>
  <div class="recipe" style="left:820px;top:2307px;width:225px;height:276px;background:linear-gradient(160deg,#6b3d1a 0%,#b5702c 45%,#3b2512 100%)" role="img" aria-label="Iced rum cocktail in a tall glass">
    <div class="recipe-caption" style="left:16px;top:213px">MET, CONSECTETUR<br>DO EIUSMOD</div>
  </div>
  <div class="recipe recipe-main" role="img" aria-label="Rum cocktail with ice and lime on a wooden board">
    <svg class="abs" style="left:192px;top:100px" width="60" height="60" viewBox="0 0 60 60"><circle cx="30" cy="30" r="27" fill="none" stroke="#fff" stroke-width="3"/><path d="M24 18 L42 30 L24 42 Z" fill="#fff"/></svg>
    <div class="recipe-caption" style="left:0;top:265px;width:100%;text-align:center;font-size:13px;line-height:22px">LOREM IPSUM DOLOR SIT AMET, CONSECTETUR<br>ADIPISCING ELIT SED DO EIUSMOD</div>
  </div>
  <div class="recipe-time">10:00 MIN</div>
  <a class="btn recipe-btn" href="#">View More</a>

  <svg class="arrow" style="left:120px;top:2424px" width="22" height="38" viewBox="0 0 22 38"><path d="M18 3 L4 19 L18 35" fill="none" stroke="#ccc" stroke-width="4" stroke-linecap="round" stroke-linejoin="round"/></svg>
  <svg class="arrow" style="left:1087px;top:2424px" width="22" height="38" viewBox="0 0 22 38"><path d="M4 3 L18 19 L4 35" fill="none" stroke="#ccc" stroke-width="4" stroke-linecap="round" stroke-linejoin="round"/></svg>
</section>

<!-- news -->
<section class="news" id="news">
  <h2 class="news-title">NEWS <b>&amp; EVENTS</b></h2>
  <div class="news-title-bar"></div>

  <article class="news-card" style="left:140px">
    <div class="news-photo" role="img" aria-label="Distillery yard with steel tanks and a windmill" style="background:linear-gradient(180deg,#9fb6c8 0%,#6f7a7e 55%,#4e5b3e 100%)"></div>
    <div class="news-date">DEC 06, 2021</div>
    <div class="news-body">
      <div class="news-head">Lorem Ipsum is simply dummy<br>text of the printing</div>
      <div class="news-text">Lorem ipsum dolor sit amet, consectetur<br>adipiscing elit, sed do eiusmod tempor</div>
      <div class="news-more">LEARN MORE &#10230;</div>
    </div>
  </article>
  <article class="news-card" style="left:464px">
    <div class="news-photo" role="img" aria-label="Row of rum barrels under palm trees" style="background:linear-gradient(180deg,#8ab6d8 0%,#5d7a52 50%,#7a5a3a 100%)"></div>
    <div class="news-date">DEC 06, 2021</div>
    <div class="news-body">
      <div class="news-head">Lorem Ipsum is simply dummy<br>text of the printing</div>
      <div class="news-text">Lorem ipsum dolor sit amet, consectetur<br>adipiscing elit, sed do eiusmod tempor</div>
      <div class="news-more">LEARN MORE &#10230;</div>
    </div>
  </article>
  <article class="news-card" style="left:787px">
    <div class="news-photo" role="img" aria-label="Glass of dark rum beside a decanter" style="background:linear-gradient(160deg,#2a2523 0%,#5a2e18 55%,#1a1615 100%)"></div>
    <div class="news-date">DEC 06, 2021</div>
    <div class="news-body">
      <div class="news-head">Lorem Ipsum is simply dummy<br>text of the printing</div>
      <div class="news-text">Lorem ipsum dolor sit amet, consectetur<br>adipiscing elit, sed do eiusmod tempor</div>
      <div class="news-more">LEARN MORE &#10230;</div>
    </div>
  </article>

  <svg class="abs" style="left:0;top:570px" width="1200" height="72" viewBox="0 0 1200 72">
    <path d="M0 45 C280 -5 520 20 720 30 C920 40 1080 25 1200 12 L1200 72 L0 72 Z" fill="#fff"/>
    <path d="M120 24 C360 0 560 22 740 28 C920 34 1060 20 1150 10" fill="none" stroke="#F7A33A" stroke-width="5" stroke-linecap="round"/>
  </svg>
</section>

<!-- footer -->
<footer>
  <div class="footer-brand">
    <div class="footer-mark"></div>
    <div class="footer-name">TIDE &amp; THISTLE</div>
    <div class="social" aria-label="Social media links"><span></span><span></span><span></span><span></span></div>
  </div>

  <div class="col-rule" style="left:423px;top:3400px;height:250px"></div>
  <div class="col-rule" style="left:662px;top:3400px;height:250px"></div>
  <div class="col-rule" style="left:879px;top:3400px;height:250px"></div>
  <div class="col-mark" style="left:423px;top:3442px"></div>
  <div class="col-mark" style="left:662px;top:3442px"></div>
  <div class="col-mark" style="left:879px;top:3442px"></div>

  <div class="footer-col" style="left:453px">
    <h4>QUICK LINKS</h4>
    <ul><li>About Us</li><li>Receipes</li><li>Products</li><li>News &amp; Events</li></ul>
  </div>
  <div class="footer-col" style="left:699px">
    <h4>RESOURCES</h4>
    <ul><li>Shipping &amp; Return</li><li>Support</li><li>Privacy Policy</li><li>Contact</li></ul>
  </div>
  <div class="footer-col contact" style="left:913px">
    <h4>CONTACT US</h4>
    <ul>
      <li><svg width="16" height="20" viewBox="0 0 16 20"><path d="M8 1 a7 7 0 0 1 7 7 c0 5 -7 11 -7 11 s-7 -6 -7 -11 a7 7 0 0 1 7 -7z" fill="#00AB8E"/><circle cx="8" cy="8" r="2.6" fill="#fff"/></svg><span>48 Harbour Lane<br>Port Ellery, IL 60912</span></li>
      <li><svg width="16" height="16" viewBox="0 0 16 16"><path d="M3 1 L6 1 L7 5 L5 6.5 C6 9 7 10 9.5 11 L11 9 L15 10 L15 13 C15 14 14 15 13 15 C6 14 2 10 1 3 C1 2 2 1 3 1Z" fill="none" stroke="#00AB8E" stroke-width="1.4"/></svg><span>(555) 204-7731</span></li>
      <li><svg width="18" height="14" viewBox="0 0 18 14"><rect x="0" y="0" width="18" height="14" rx="1.5" fill="#00AB8E"/><path d="M1 1.5 L9 8 L17 1.5" fill="none" stroke="#fff" stroke-width="1.4"/></svg><span>hello@tideandthistle.com</span></li>
    </ul>
  </div>

  <div class="footer-line"></div>
  <div class="copyright">© 2021 Tide &amp; Thistle | All Rights Reserved</div>
</footer>

</body>
</html>
```